Black Matte card with samurai logo which I would like it to be textured and company name on one side and on the other side I would like the company information with the reno (Face logo) Sushi logo. Double Sided card.

majority customers are University students, University sororities and fraternities.

It Company

Reno Sushi
317 W. Harlow Ave
Tucson, AZ 85042
Phone (520)413-6271
Fax (520)357-1846
E-mail: Renosushidesert@mailbox-example.com
FB: Renosushidesert
Twitter: Renosushidesert

• Present Normal

```html
<!DOCTYPE html>
<html lang="en">
<head>
<meta charset="utf-8">
<title>Reno Sushi – Business Card</title>
<link href="https://fonts.googleapis.com/css2?family=Source+Sans+3:wght@400&display=swap" rel="stylesheet">
<style>
  :root {
    --page: #ecebe8;
    --card-black: #141414;
    --card-black-edge: #050505;
    --card-white: #ffffff;
    --brand-red: #c8102e;
    --ink: #454545;
    --ghost: #ececec;
    --ghost-red: #f6e3e3;
    --icon-square: #7a8fb5;
  }
  html, body {
    margin: 0;
    width: 1200px;
    height: 1010px;
    overflow: hidden;
    background: var(--page);
    font-family: "Source Sans 3", "Myriad Pro", sans-serif;
  }
  .canvas { position: relative; width: 1200px; height: 1010px; }
  .card {
    position: absolute;
    width: 771px;
    height: 440px;
    box-sizing: border-box;
    overflow: hidden;
  }
  .card--front {
    left: 40px; top: 56px;
    background: radial-gradient(ellipse at 50% 45%, #2c2c2c 0%, var(--card-black) 55%, var(--card-black-edge) 100%);
  }
  .card--back {
    left: 355px; top: 523px;
    background: var(--card-white);
    border: 1px solid #222;
  }
  .mascot-area {
    position: absolute;
    left: 253px; top: 54px;
    width: 258px; height: 233px;
    background: radial-gradient(circle at 50% 45%, #6a6a6a 0%, #3a3a3a 60%, rgba(40,40,40,0) 100%);
    border-radius: 8px;
  }
  .wordmark {
    position: absolute;
    left: 0; right: 0; top: 300px;
    text-align: center;
    color: var(--brand-red);
    font-size: 78px;
    line-height: 1;
    letter-spacing: 1px;
  }
  .mascot-ghost {
    position: absolute;
    left: 133px; top: 0;
    width: 489px; height: 440px;
    background: linear-gradient(180deg, var(--ghost) 0%, var(--ghost-red) 55%, var(--ghost) 100%);
    opacity: .8;
  }
  .contact {
    position: absolute;
    left: 0; right: 0; top: 144px;
    margin: 0; padding: 0;
    list-style: none;
    color: var(--ink);
    font-size: 24px;
    line-height: 38px;
    text-align: center;
  }
  .contact li { display: flex; justify-content: center; align-items: center; gap: 10px; }
  .contact svg { width: 22px; height: 22px; flex: none; }
  .square { width: 22px; height: 22px; background: var(--icon-square); flex: none; }
  .address {
    position: absolute;
    left: 0; right: 0; top: 362px;
    margin: 0;
    text-align: center;
    color: var(--ink);
    font-size: 24px;
  }
</style>
</head>
<body>
<div class="canvas">
  <section class="card card--front">
    <div class="mascot-area" role="img" aria-label="Samurai warrior mascot holding a sword and a fish"></div>
    <div class="wordmark">reno sushi</div>
  </section>

  <section class="card card--back">
    <div class="mascot-ghost" role="img" aria-label="Faint samurai mascot background decoration"></div>
    <ul class="contact">
      <li>
        <svg viewBox="0 0 24 24" aria-hidden="true"><path d="M6 3l3 4-2 2c1 3 4 6 7 7l2-2 4 3-2 3C10 20 4 14 3 5z" fill="none" stroke="#454545" stroke-width="1.6"/></svg>
        (520)413-6271
      </li>
      <li>
        <svg viewBox="0 0 24 24" aria-hidden="true"><rect x="7" y="3" width="10" height="18" rx="1.5" fill="#454545"/><rect x="9" y="5" width="6" height="5" fill="#fff"/><g fill="#fff"><rect x="9" y="12" width="2" height="2"/><rect x="13" y="12" width="2" height="2"/><rect x="9" y="16" width="2" height="2"/><rect x="13" y="16" width="2" height="2"/></g></svg>
        (520)357-1846
      </li>
      <li>
        <svg viewBox="0 0 24 24" aria-hidden="true"><path d="M3 9l9-5 9 5v10H3z" fill="#454545"/><path d="M3 9l9 6 9-6" fill="none" stroke="#fff" stroke-width="1.4"/></svg>
        Renosushidesert@mailbox-example.com
      </li>
      <li><span class="square"></span>Renosushidesert</li>
      <li><span class="square"></span>Renosushidesert</li>
    </ul>
    <p class="address">Reno Sushi 317 W. Harlow Ave Tucson, AZ 85042</p>
  </section>
</div>
</body>
</html>
```